The Linen Loft Co

We need a business card design for our wardrobe company.
Please visit our website www.gentlelinenlofts.com to get an idea of who we are.

```html
<!DOCTYPE html>
<html lang="en">
<head>
<meta charset="utf-8">
<title>The Linen Loft Co – Business Card</title>
<link rel="stylesheet" href="https://fonts.googleapis.com/css2?family=Lato:wght@400;700&display=swap">
<style>
  :root {
    --backdrop: #e4e4e4;
    --card-white: #ffffff;
    --ink: #141414;
    --panel: #161616;
    --panel-text: #f2f2f2;
    --panel-muted: #d6d6d6;
  }
  * { margin: 0; padding: 0; box-sizing: border-box; }
  html, body {
    width: 1200px;
    height: 900px;
    overflow: hidden;
    background: var(--backdrop);
    font-family: "Lato", sans-serif;
  }
  .canvas {
    position: relative;
    width: 1200px;
    height: 900px;
  }
  .card {
    position: absolute;
    width: 520px;
    height: 300px;
    border-radius: 26px;
    overflow: hidden;
    background: var(--card-white);
    box-shadow: 0 10px 24px rgba(0, 0, 0, 0.18);
  }
  .card--front { left: 80px; top: 140px; }
  .card--back { left: 600px; top: 460px; }

  /* Front */
  .brand {
    position: absolute;
    inset: 0;
    display: flex;
    align-items: center;
    justify-content: center;
    gap: 16px;
    color: var(--ink);
  }
  .brand__square {
    width: 44px;
    height: 44px;
    background: var(--ink);
  }
  .brand__name {
    font-weight: 700;
    font-size: 17px;
    letter-spacing: 0.5px;
    text-transform: uppercase;
    line-height: 1.2;
  }
  .brand__tagline {
    font-weight: 400;
    font-size: 14px;
    line-height: 1.3;
  }

  /* Back */
  .back-art {
    position: absolute;
    inset: 0;
    width: 520px;
    height: 300px;
  }
  .contact {
    position: absolute;
    right: 26px;
    top: 56px;
    text-align: right;
    color: var(--panel-text);
  }
  .contact__name {
    font-weight: 700;
    font-size: 18px;
    letter-spacing: 0.5px;
    text-transform: uppercase;
    line-height: 1.1;
  }
  .contact__role {
    font-size: 13px;
    color: var(--panel-muted);
    margin-bottom: 8px;
  }
  .contact__line {
    font-size: 13px;
    line-height: 1.45;
    display: flex;
    justify-content: flex-end;
    align-items: center;
    gap: 6px;
  }
  .contact__line--gap { margin-top: 10px; }
  .contact__icon {
    width: 11px;
    height: 11px;
    flex: none;
  }
</style>
</head>
<body>
<main class="canvas">

  <section class="card card--front" aria-label="Business card front">
    <div class="brand">
      <div class="brand__square"></div>
      <div class="brand__text">
        <p class="brand__name">The Linen Loft Co</p>
        <p class="brand__tagline">Folded Neat, Stored Right</p>
      </div>
    </div>
  </section>

  <section class="card card--back" aria-label="Business card back">
    <svg class="back-art" viewBox="0 0 520 300" aria-hidden="true">
      <path d="M212 0 H520 V300 H118 C168 228 196 122 212 0 Z" fill="var(--panel)"/>
      <path d="M226 0 C212 120 186 228 136 300" fill="none" stroke="var(--card-white)" stroke-width="3"/>
    </svg>
    <div class="contact">
      <p class="contact__name">Daniel Hartley</p>
      <p class="contact__role">Managing Director</p>
      <p class="contact__line">Orchard Court, 42 Mill Lane</p>
      <p class="contact__line">London N4 7QB</p>
      <p class="contact__line">0208 415 6273
        <svg class="contact__icon" viewBox="0 0 12 12" aria-hidden="true"><path d="M2 1h3l1 3-1.5 1a6 6 0 0 0 2.5 2.5L8 6l3 1v3a1 1 0 0 1-1 1A9 9 0 0 1 1 2a1 1 0 0 1 1-1z" fill="currentColor"/></svg>
      </p>
      <p class="contact__line contact__line--gap">info@gentlelinenlofts.com
        <svg class="contact__icon" viewBox="0 0 12 12" aria-hidden="true"><rect x="1" y="2.5" width="10" height="7" fill="currentColor"/><path d="M1 2.5l5 4 5-4" fill="none" stroke="var(--panel)" stroke-width="1"/></svg>
      </p>
      <p class="contact__line">www.gentlelinenlofts.com
        <svg class="contact__icon" viewBox="0 0 12 12" aria-hidden="true"><circle cx="6" cy="6" r="5" fill="currentColor"/><path d="M1 6h10M6 1c-2 2.5-2 7.5 0 10M6 1c2 2.5 2 7.5 0 10" fill="none" stroke="var(--panel)" stroke-width="0.8"/></svg>
      </p>
    </div>
  </section>

</main>
</body>
</html>
```